Naturopath Practitioner Card Design

I am a naturopath needing a design for a business card mainly to show that I am a naturopath and have some contact details to give to prospective clients. I am open minded about the design and what is on the second side of the card whether it just be some artwork or space for details, appointment times etc. Naturopathy is the practice of natural medicine that uses a holistic approach and incorporates herbal and nutritional medicine.

Industry/Entity Type

Business

Contact Information for Business Card

Tom Rudd NaturopathBHSc (Naturopathy) Member WHPG 0487 925 316 tom.rudd@mailexample.com www.tomruddnaturopathy.example.au

Requirements
Nice to have
• Would prefer some kind of original pattern/art work/logo rather than an image, not fussed if its very simple/basic
• I am open to any colour but think I would prefer a more earthy sandy clay etc type style than the greens that are commonly associated with naturopathy.
Should not have
• Don't really want to have generic stock images on it

```html
<!DOCTYPE html>
<html lang="en">
<head>
<meta charset="utf-8">
<title>Tom Rudd Naturopath – Business Card</title>
<link rel="stylesheet" href="https://fonts.googleapis.com/css2?family=Source+Sans+3:wght@400;600;700&display=swap">
<style>
  :root {
    --bg: #ecebe8;
    --card: #ffffff;
    --green-light: #8fdc12;
    --green-bright: #2fcc12;
    --green-deep: #1f8a0e;
    --green-text: #2aa814;
    --ink: #1b1b1b;
    --box: #8a8a8a;
  }
  * { margin: 0; padding: 0; box-sizing: border-box; }
  html, body { width: 1200px; height: 900px; overflow: hidden; }
  body {
    background: var(--bg);
    font-family: "Source Sans 3", "Myriad Pro", Arial, sans-serif;
    position: relative;
  }
  .card {
    position: absolute;
    background: var(--card);
    overflow: hidden;
    box-shadow: 0 6px 18px rgba(0,0,0,.18);
  }

  /* Front */
  .card-front { left: 78px; top: 34px; width: 588px; height: 364px; }
  .leaf-art {
    position: absolute; left: 0; top: 0; width: 420px; height: 230px;
    background:
      radial-gradient(ellipse 60% 55% at 35% 40%, rgba(160,225,40,.95), rgba(190,235,120,.5) 55%, rgba(255,255,255,0) 80%),
      linear-gradient(90deg, #b9df8a 0%, #e6f1d8 55%, #ffffff 100%);
  }
  .front-bands { position: absolute; left: 0; top: 0; width: 588px; height: 364px; }
  .contact {
    position: absolute; right: 334px; top: 264px;
    color: #fff; font-size: 16px; text-align: right; line-height: 25px;
  }
  .contact-line { display: flex; align-items: center; justify-content: flex-end; gap: 6px; }
  .contact-line svg { width: 12px; height: 12px; }
  .identity { position: absolute; left: 296px; top: 248px; color: #fff; }
  .identity-name { font-size: 23px; font-weight: 700; line-height: 28px; }
  .identity-role, .identity-cred { font-size: 16px; line-height: 27px; }
  .identity-role { margin-top: 1px; }

  /* Back */
  .card-back { left: 388px; top: 505px; width: 567px; height: 352px; }
  .appt-title {
    position: absolute; top: 42px; width: 100%; text-align: center;
    color: var(--green-text); font-size: 23px; font-weight: 600;
  }
  .field {
    position: absolute; left: 72px; color: var(--ink);
    font-size: 16px; font-weight: 600; white-space: nowrap;
  }
  .field-name { top: 106px; }
  .field-date { top: 170px; }
  .dots { font-weight: 400; letter-spacing: .5px; }
  .days {
    position: absolute; left: 50px; top: 230px; display: flex; gap: 0;
  }
  .day {
    width: 83px; display: flex; align-items: center; gap: 6px;
    color: var(--green-text); font-size: 15px;
  }
  .day-box { width: 20px; height: 18px; border: 1.5px solid var(--box); }
  .notice {
    position: absolute; left: 0; bottom: 0; width: 100%; height: 70px;
    background: linear-gradient(180deg, var(--green-bright), var(--green-deep));
    color: #fff; font-size: 18px; font-weight: 600;
    display: flex; align-items: center; justify-content: center; padding-bottom: 16px;
  }
</style>
</head>
<body>

<section class="card card-front">
  <div class="leaf-art" role="img" aria-label="Photograph of fresh green tea leaves"></div>
  <svg class="front-bands" viewBox="0 0 588 364" aria-hidden="true">
    <defs>
      <linearGradient id="deep" x1="0" y1="0" x2="0" y2="1">
        <stop offset="0" stop-color="#2fcc12"/>
        <stop offset="1" stop-color="#1f8a0e"/>
      </linearGradient>
    </defs>
    <polygon points="0,200 402,200 380,226 0,226" fill="var(--green-light)"/>
    <polygon points="0,229 384,229 416,191 588,191 588,364 0,364" fill="url(#deep)"/>
    <polyline points="382,228 414,190 588,190" fill="none" stroke="#ffffff" stroke-width="2"/>
  </svg>
  <div class="contact">
    <div class="contact-line">0487 925 316
      <svg viewBox="0 0 12 12"><path d="M2.5 1 L4.5 1 L5.3 3.5 L4 4.5 Q5 7 7.5 8 L8.5 6.7 L11 7.5 L11 9.5 Q10 11 8.5 11 Q1 9.5 1 2.5 Q1 1 2.5 1Z" fill="#fff"/></svg>
    </div>
    <div class="contact-line">tom.rudd@mailexample.com
      <svg viewBox="0 0 12 12"><rect x="1" y="2.5" width="10" height="7" fill="#fff"/><polyline points="1,2.5 6,6.5 11,2.5" fill="none" stroke="#1f8a0e" stroke-width="1"/></svg>
    </div>
  </div>
  <div class="identity">
    <div class="identity-name">Tom Rudd</div>
    <div class="identity-role">Naturopath</div>
    <div class="identity-cred">BHSc (Naturopathy) Member WHPG</div>
  </div>
</section>

<section class="card card-back">
  <h2 class="appt-title">Your Next Appointment on</h2>
  <div class="field field-name">Name : <span class="dots">..........................................................................</span></div>
  <div class="field field-date">Date : <span class="dots">..............................</span> &nbsp;Time : <span class="dots">............................</span> <span class="dots">AM / PM</span></div>
  <div class="days">
    <div class="day"><span class="day-box"></span>MON</div>
    <div class="day"><span class="day-box"></span>TUE</div>
    <div class="day"><span class="day-box"></span>WED</div>
    <div class="day"><span class="day-box"></span>THU</div>
    <div class="day"><span class="day-box"></span>FRI</div>
    <div class="day"><span class="day-box"></span>SAT</div>
  </div>
  <div class="notice">If unable to keep appointment,&nbsp; kindly give 24hrs notice.</div>
</section>

</body>
</html>
```